Business Cards Design for the electrical wholesaler: clean bold dynamic :)

We need a business card design that would follow our latest brand guidelines. As an electrical wholesaler we want to bring a fresh look and feel into the industry. The design should be clean bold and dynamic. It should come alive with the renewed energy of our green colour. Our grey colour should keep things balanced and complement the notion of maturity and responsibility. We employ Lato as a corporate font however are not bound by this font and we’re open to interpretation here.

Target Market(s)

Electrical contractors

Industry/Entity Type

Business

Contact Information for Business Card

Logo
Name & Surname: Halyna Dorosh
Job Title: Director of Marketing
Email: halya.dorosh@quillmail.example
Cell phone: XXX.XXX.XXXX
Address: 20517 - 87 Ave. Edmonton, AB, Canada. T6K 4N8
Business Phone: 780.555.0184
Website: www.brovix.example

Font styles to use
Other font styles liked:
• Lato

Requirements
Must have
• Logo & website
Nice to have
• Brand elements - some of them you may find in the attached Brand Guidelines (e.g. three lines on the background signifying "W")

```html
<!DOCTYPE html>
<html lang="en">
<head>
<meta charset="utf-8">
<title>Brovix Business Card – Halyna Dorosh</title>
<link rel="stylesheet" href="https://fonts.googleapis.com/css2?family=Source+Sans+3:wght@400;600&display=swap">
<style>
  :root {
    --brand-green: #6cbe1e;
    --brand-grey: #454b4e;
    --text-grey: #2f3437;
    --muted-grey: #5d6366;
    --card-white: #f6f6f6;
    --backdrop: #e6e6e6;
    --white: #ffffff;
  }
  * { box-sizing: border-box; margin: 0; padding: 0; }
  html, body {
    width: 1200px; height: 901px; overflow: hidden;
    background: var(--backdrop);
    font-family: "Source Sans 3", "Lato", sans-serif;
  }
  .card {
    position: absolute; left: 235px;
    width: 730px; height: 417px;
    box-shadow: 0 2px 6px rgba(0,0,0,0.14);
    overflow: hidden;
  }

  /* Back side */
  .card-back { top: 22px; background: var(--brand-grey); }
  .back-lockup {
    position: absolute; left: 40px; top: 36px;
    display: flex; flex-direction: column; align-items: flex-end;
  }
  .back-lockup .brand-row { display: flex; align-items: center; gap: 12px; }
  .back-lockup .brand-dot {
    width: 34px; height: 34px; border-radius: 50%; background: var(--brand-green);
  }
  .back-lockup .brand-name {
    font-size: 46px; font-weight: 400; line-height: 1; color: var(--white);
  }
  .back-lockup .brand-tagline {
    margin-top: 3px; font-size: 8px; font-weight: 600;
    letter-spacing: 1.2px; color: var(--white);
  }

  /* Front side */
  .card-front { top: 462px; background: var(--card-white); }
  .brand-lockup {
    position: absolute; left: 40px; top: 176px; width: 265px;
    display: flex; flex-direction: column; align-items: flex-end;
  }
  .brand-lockup .brand-row { display: flex; align-items: center; gap: 12px; }
  .brand-lockup .brand-dot {
    width: 41px; height: 41px; border-radius: 50%; background: var(--brand-green);
  }
  .brand-lockup .brand-name {
    font-size: 56px; font-weight: 400; line-height: 1; color: var(--brand-grey);
  }
  .brand-lockup .brand-tagline {
    margin-top: 3px; font-size: 9.5px; font-weight: 600;
    letter-spacing: 1.1px; color: var(--brand-grey);
  }
  .divider {
    position: absolute; left: 349px; top: 43px;
    width: 1.5px; height: 310px; background: var(--muted-grey);
  }
  .contact-block { position: absolute; left: 378px; top: 42px; }
  .person-name {
    font-size: 24.5px; font-weight: 600; color: var(--brand-green); line-height: 1.15;
  }
  .person-title {
    font-size: 19px; font-weight: 400; color: var(--muted-grey); line-height: 1.3;
  }
  .address {
    position: absolute; left: 378px; top: 136px;
    font-size: 19px; line-height: 26.5px; color: var(--text-grey); font-style: normal;
  }
  .contact-list { position: absolute; left: 378px; top: 212px; list-style: none; }
  .contact-list li {
    display: flex; align-items: center; height: 35px;
    font-size: 19px; color: var(--text-grey); letter-spacing: 0.3px;
  }
  .contact-list .icon { width: 36px; display: flex; align-items: center; }
  .contact-list svg { fill: var(--brand-green); stroke: var(--brand-green); }
  .footer-band {
    position: absolute; left: 0; top: 373px;
    width: 100%; height: 29px; background: var(--brand-grey);
  }
</style>
</head>
<body>
  <section class="card card-back" aria-label="Card back">
    <div class="back-lockup">
      <div class="brand-row">
        <span class="brand-dot"></span>
        <span class="brand-name">brovix</span>
      </div>
      <span class="brand-tagline">ELECTRICAL&nbsp; WHOLESALERS</span>
    </div>
  </section>

  <main class="card card-front" aria-label="Card front">
    <div class="brand-lockup">
      <div class="brand-row">
        <span class="brand-dot"></span>
        <span class="brand-name">brovix</span>
      </div>
      <span class="brand-tagline">ELECTRICAL&nbsp; WHOLESALERS</span>
    </div>

    <div class="divider"></div>

    <header class="contact-block">
      <h1 class="person-name">Halyna Dorosh</h1>
      <p class="person-title">Director of Marketing</p>
    </header>

    <address class="address">
      20517 - 87 Ave. Edmonton<br>
      AB Canada. T6K 4N8
    </address>

    <ul class="contact-list">
      <li>
        <span class="icon">
          <svg width="25" height="25" viewBox="0 0 38 38">
            <circle cx="19" cy="19" r="16" fill="none" stroke-width="3"/>
            <path d="M12 11c1-1 3-1 4 0l2 3c.6 1 .3 2-.5 2.6l-1 .8c1 2.4 2.8 4.2 5.2 5.2l.8-1c.6-.8 1.6-1.1 2.6-.5l3 2c1 1 1 3 0 4-2 2-5 2-8.5 0-3-1.8-5.5-4.3-7.2-7.3-2-3.5-2-6.8-.4-8.8z" stroke="none"/>
          </svg>
        </span>
        780.555.0184
      </li>
      <li>
        <span class="icon">
          <svg width="17" height="27" viewBox="0 0 26 40">
            <rect x="2" y="2" width="22" height="36" rx="3" fill="none" stroke-width="3"/>
            <line x1="2" y1="31" x2="24" y2="31" stroke-width="2"/>
            <circle cx="13" cy="34.5" r="1.6" stroke="none"/>
          </svg>
        </span>
        780.555.0147
      </li>
      <li>
        <span class="icon">
          <svg width="20" height="15" viewBox="0 0 30 22">
            <rect x="1" y="1" width="28" height="20" stroke="none"/>
            <path d="M1 1l14 11L29 1" fill="none" stroke="#f6f6f6" stroke-width="2"/>
          </svg>
        </span>
        halya.dorosh@quillmail.example
      </li>
      <li>
        <span class="icon">
          <svg width="19" height="19" viewBox="0 0 30 30">
            <circle cx="15" cy="15" r="13" stroke="none"/>
            <path d="M2 15h26M15 2c-5 5-5 21 0 26M15 2c5 5 5 21 0 26" fill="none" stroke="#f6f6f6" stroke-width="1.6"/>
          </svg>
        </span>
        www.brovix.example
      </li>
    </ul>

    <div class="footer-band"></div>
  </main>
</body>
</html>
```